Stylish new business card needed!

Hello everyone! I am in need of a new business card design for an alarm company here in Hurricane WV. I have all fonts, color codes and logos provided for you use! We are a young company and like the style of a clean sleek looking business card. Would like it double sided, one side holding the logo and the other with your design!
Target Market(s)
The people that are looking for the newest tech for home automation and security
Industry/Entity Type
Alarm services; Home automation
Contact Information for Business Card
Name of person; position (Sales; Installer); Phone Number (555.418.7260); Employee cell Number; Website (www.GuardedByVelk.example); Employee Email; Double sided
Look and feel
Each slider illustrates characteristics of the customer's brand and the style your logo design should communicate.

```html
<!DOCTYPE html>
<html lang="en">
<head>
<meta charset="utf-8">
<title>Velk Business Card</title>
<link rel="stylesheet" href="https://fonts.googleapis.com/css2?family=Archivo+Black&family=Arimo:wght@400;700&display=swap">
<style>
  :root {
    --bg: #141414;
    --card-dark: #292929;
    --card-light: #f6f5f2;
    --orange: #f47b3a;
    --ink: #2b2b2b;
    --white: #ffffff;
  }
  * { box-sizing: border-box; margin: 0; padding: 0; }
  html, body { width: 1200px; height: 963px; overflow: hidden; }
  body {
    background: var(--bg);
    display: flex;
    flex-direction: column;
    align-items: center;
    justify-content: center;
    gap: 60px;
  }
  .card {
    width: 700px;
    height: 400px;
    border-radius: 28px;
    overflow: hidden;
    background: var(--card-dark);
    box-shadow: 0 0 0 2px var(--orange), 0 18px 40px rgba(0,0,0,.55);
    display: flex;
  }
  /* Front */
  .brand-panel {
    width: 300px;
    background: var(--card-light);
    display: flex;
    flex-direction: column;
    align-items: center;
    justify-content: center;
    gap: 16px;
  }
  .brand-name {
    font-family: "Arimo", sans-serif;
    font-weight: 700;
    font-size: 64px;
    line-height: 1;
    color: var(--ink);
  }
  .tagline {
    font-family: "Archivo Black", sans-serif;
    font-size: 10px;
    letter-spacing: 1px;
    text-transform: uppercase;
    color: var(--orange);
  }
  .contact-panel {
    flex: 1;
    padding: 60px 0 0 70px;
    color: var(--white);
    font-family: "Arimo", sans-serif;
  }
  .person-name {
    font-family: "Archivo Black", sans-serif;
    font-size: 28px;
    color: var(--orange);
    text-transform: uppercase;
    letter-spacing: 0.5px;
  }
  .person-role { font-size: 21px; margin-top: 4px; }
  .icon-row { display: flex; gap: 14px; margin: 30px 0 26px; }
  .icon-row svg { width: 34px; height: 34px; }
  .contact-line { font-size: 20px; line-height: 1.6; }
  /* Back */
  .card--back {
    align-items: center;
    justify-content: center;
  }
  .card--back .brand-name {
    font-size: 96px;
    color: var(--white);
  }
</style>
</head>
<body>
  <section class="card card--front">
    <div class="brand-panel">
      <div class="brand-name">Velk</div>
      <div class="tagline">Automation and security services</div>
    </div>
    <div class="contact-panel">
      <div class="person-name">Daniel Marsh</div>
      <div class="person-role">Sales / Installer</div>
      <div class="icon-row">
        <svg viewBox="0 0 34 34" aria-label="Phone"><circle cx="17" cy="17" r="15" fill="none" stroke="var(--orange)" stroke-width="2"/><path d="M12 10c-1 1-1.5 3 0 6s4 6 7 7.5c2 1 3.5.5 4.5-.5l-2.5-2.5-2 1c-1.5-.8-3.5-2.8-4.3-4.3l1-2L13 10z" fill="var(--orange)"/></svg>
        <svg viewBox="0 0 34 34" aria-label="Email"><circle cx="17" cy="17" r="15" fill="none" stroke="var(--orange)" stroke-width="2"/><rect x="10" y="12" width="14" height="10" fill="none" stroke="var(--orange)" stroke-width="1.6"/><path d="M10 12l7 6 7-6" fill="none" stroke="var(--orange)" stroke-width="1.6"/></svg>
        <svg viewBox="0 0 34 34" aria-label="Website"><circle cx="17" cy="17" r="15" fill="none" stroke="var(--orange)" stroke-width="2"/><circle cx="17" cy="17" r="8" fill="none" stroke="var(--orange)" stroke-width="1.6"/><ellipse cx="17" cy="17" rx="3.5" ry="8" fill="none" stroke="var(--orange)" stroke-width="1.4"/><path d="M9 17h16M10.5 13h13M10.5 21h13" stroke="var(--orange)" stroke-width="1.2"/></svg>
      </div>
      <div class="contact-line">555.418.7260</div>
      <div class="contact-line">info@GuardedByVelk.example</div>
      <div class="contact-line">www.GuardedByVelk.example</div>
    </div>
  </section>

  <section class="card card--back">
    <div class="brand-name">Velk</div>
  </section>
</body>
</html>
```